Prayer Service 12.28.2013

I need a flyer designed for a Christian prayer service. The title and theme is:
"Total and Complete Surrender for Total and Complete Deliverance!"
1. You have creative freedom with imagery and typography
2. I need a quick turnaround time
FLYER DETAILS:
A prayer, anointing, and deliverance all night prayer service, at Valleybrook Assembly.
Saturday December 28 2013 from 9pm-6am.
Special guest speakers, prayer,anointing,and deliverance sessions.
For more information contact Sis Rosalind Okafor at Valleybrook Assembly 347 562 9140 Ext. 4816 or Marlene Cobb at 631 208-4392

```html
<!DOCTYPE html>
<html lang="en">
<head>
<meta charset="utf-8">
<title>Total and Complete Surrender — All Night Prayer Service</title>
<link rel="stylesheet" href="https://fonts.googleapis.com/css2?family=Arimo:ital,wght@0,400;0,700;1,400&family=Cinzel:wght@600&display=swap">
<style>
  :root {
    --ink: #111111;
    --band: #000000;
    --paper: #ffffff;
    --muted: #8e8e8e;
    --veil: rgba(255,255,255,0.78);
    --veil-soft: rgba(255,255,255,0.62);
    --photo-light: #ece8e3;
    --photo-mid: #b9aba0;
    --photo-dark: #4a3228;
  }
  * { margin: 0; padding: 0; box-sizing: border-box; }
  html, body { width: 834px; height: 1200px; overflow: hidden; background: var(--paper); }
  .flyer { position: relative; width: 834px; height: 1200px; overflow: hidden; font-family: "Arimo", Arial, sans-serif; color: var(--ink); }

  .hero-photo {
    position: absolute; left: 0; top: 0; width: 834px; height: 873px;
    background:
      radial-gradient(ellipse 260px 330px at 600px 430px, var(--photo-dark) 0%, rgba(74,50,40,0.85) 55%, rgba(74,50,40,0) 100%),
      radial-gradient(ellipse 300px 240px at 620px 140px, #1e1511 0%, rgba(30,21,17,0) 100%),
      linear-gradient(90deg, var(--photo-light) 0%, #ddd6cf 35%, var(--photo-mid) 60%, #8d7466 100%);
  }
  .veil { position: absolute; left: 0; top: 0; width: 834px; height: 873px; }

  .contact {
    position: absolute; left: 52px; top: 56px;
    font-size: 21px; line-height: 25.5px; color: var(--muted);
  }

  .when { position: absolute; left: 53px; top: 494px; }
  .when-day { font-size: 48px; font-weight: 700; line-height: 56px; letter-spacing: -0.5px; }
  .when-date { font-size: 27px; font-weight: 700; line-height: 38px; margin-top: 10px; }
  .when-highlights { font-size: 29.5px; font-style: italic; line-height: 36px; margin-top: 30px; }

  .band { position: absolute; left: 0; top: 873px; width: 834px; height: 327px; background: var(--band); color: var(--paper); }
  .band-title {
    position: absolute; left: 72px; top: 36px;
    font-family: "Cinzel", "Times New Roman", serif; font-weight: 600;
    font-size: 41px; line-height: 62px; letter-spacing: 0.5px;
  }
  .band-title .cap { font-size: 49px; }
  .band-sub {
    position: absolute; left: 72px; top: 226px;
    font-family: "Cinzel", "Times New Roman", serif; font-weight: 600;
    font-size: 17px; line-height: 32px; letter-spacing: 2.6px;
  }
  .band-sub .cap { font-size: 21px; }
</style>
</head>
<body>
<main class="flyer">
  <div class="hero-photo" role="img" aria-label="Photograph of a woman resting her chin on folded hands in prayer, with soft glowing candles behind her"></div>

  <svg class="veil" viewBox="0 0 834 873" aria-hidden="true">
    <path d="M0 0 H370 C395 80 360 170 300 250 C250 320 215 380 170 412 C110 420 50 420 0 418 Z" fill="var(--veil)"/>
    <path d="M0 418 C150 400 300 420 400 490 C480 550 520 640 520 760 V873 H0 Z" fill="var(--veil-soft)"/>
  </svg>

  <p class="contact">
    For more information<br>
    contact Sis Rosalind<br>
    Okafor at<br>
    Valleybrook<br>
    Assembly 347 562<br>
    9140 Ext. 4816<br>
    or Marlene Cobb<br>
    at 631 208-4392
  </p>

  <section class="when">
    <h2 class="when-day">Saturday</h2>
    <p class="when-date">December 28 2013<br>from 9pm-6am.</p>
    <p class="when-highlights">Special guest speakers,<br>prayer, anointing, and<br>deliverance sessions.</p>
  </section>

  <footer class="band">
    <h1 class="band-title">
      <span class="cap">T</span>otal and <span class="cap">C</span>omplete<br>
      <span class="cap">S</span>urrender for <span class="cap">T</span>otal and<br>
      <span class="cap">C</span>omplete <span class="cap">D</span>eliverance!
    </h1>
    <p class="band-sub">
      <span class="cap">A</span> prayer, anointing, and deliverance all night<br>
      prayer service, at <span class="cap">V</span>alleybrook <span class="cap">A</span>ssembly.
    </p>
  </footer>
</main>
</body>
</html>
```